Halvick Ledgers & Advisory Tri-Fold Brochure (8.5"x11")

I need a professional looking brochure for my bookkeeping business. I am looking for something professional yet casual (not too corporate looking). I have attached a sample brochure that will outline the areas and a copy of our logo. I'd like to stick with shades of blue. The final product should communicate professional and personal.

Target Market(s)

Small service businesses.

Industry/Entity Type

Business

Font styles to use
Sans Serif

Requirements
Must have
• Professional looking photos of people in areas where it asks for a picture.

```html
<!DOCTYPE html>
<html lang="en">
<head>
<meta charset="utf-8">
<title>Halvick Ledgers & Advisory – Tri-Fold Brochure</title>
<link rel="stylesheet" href="https://fonts.googleapis.com/css2?family=Exo+2:wght@400;500;600;700&display=swap">
<style>
:root{
  --blue:#3aa6dc;
  --blue-deep:#2b8fc6;
  --ink:#3c3d40;
  --charcoal:#404144;
  --paper:#ffffff;
  --mist:#eef0f2;
  --stage:#e6e8eb;
  --text:#4a4b4e;
}
*{box-sizing:border-box;margin:0;padding:0}
html,body{width:1200px;height:900px;overflow:hidden}
body{background:var(--stage);font-family:"Exo 2",sans-serif;color:var(--text);position:relative}
.spread{position:absolute;top:234px;width:560px;height:433px;display:flex;box-shadow:0 6px 18px rgba(0,0,0,.12);background:var(--paper)}
.spread--outside{left:30px}
.spread--inside{left:610px}
.panel{width:186.67px;height:100%;position:relative;display:flex;flex-direction:column;align-items:center;overflow:hidden}
.panel + .panel{border-left:1px solid #e3e5e8}

/* shared pieces */
.icon-badge{width:50px;height:50px;border-radius:50%;background:var(--paper);display:flex;align-items:center;justify-content:center;box-shadow:0 0 0 3px var(--blue),0 0 0 4px rgba(255,255,255,.8)}
.band-dark{background:var(--charcoal);color:#fff;text-align:center}
.band-blue{background:var(--blue);color:#fff;text-align:center}
.brand-name{font-weight:600;letter-spacing:.5px}
.copy{font-size:6.6px;line-height:1.45}

/* outside: what we do */
.panel--intro{background:var(--blue);color:#fff;padding:20px 0 0;border:6px solid var(--paper)}
.panel--intro .icon-badge{margin-bottom:12px}
.intro-title{font-size:13.5px;font-weight:500;text-align:center;line-height:1.15;padding:0 12px;text-transform:uppercase}
.intro-label{width:100%;font-size:7.5px;padding:3px 0;margin:8px 0 7px}
.intro-copy{padding:0 12px;text-align:center}
.panel--intro .brand-name{font-size:22px;margin-top:auto;margin-bottom:10px;color:#fff}
.talk{width:100%;padding:7px 0 8px}
.talk-title{font-size:22px;font-weight:600;letter-spacing:1px;line-height:1}
.talk-sub{font-size:7px;margin-top:2px}

/* outside: back panel */
.panel--back{background:linear-gradient(150deg,#fdfdfd 0%,#e7e9ec 60%,#f6f7f8 100%);padding:8px}
.back-frame{border:1px solid var(--blue);width:100%;height:100%;display:flex;flex-direction:column;align-items:center;padding-top:44px}
.panel--back .brand-name{font-size:26px;color:var(--blue)}
.tagline-small{font-size:8.5px;font-weight:500;color:var(--ink);margin-top:50px;text-transform:uppercase;letter-spacing:.4px}
.tagline-big{font-size:29px;font-weight:600;color:var(--ink);letter-spacing:1px;line-height:1}
.contact{margin-top:auto;text-align:center;padding-bottom:14px}
.contact-title{font-size:11px;color:var(--ink);font-weight:500}
.contact-line{font-size:7.2px;color:var(--blue-deep);line-height:1.35}
.contact-phone{font-size:17px;font-weight:600;color:var(--ink);margin-top:5px}

/* outside: front cover */
.panel--cover{background:var(--blue);padding:5px}
.cover-inner{background:var(--mist);width:100%;height:100%;display:flex;flex-direction:column;align-items:center;padding-top:22px}
.panel--cover .brand-name{font-size:24px;color:var(--blue-deep)}
.cover-line{font-size:8.3px;color:var(--ink);text-transform:uppercase;line-height:1.2;text-align:center}
.cover-line--strong{font-size:10.5px;font-weight:500}
.cover-band{width:100%;font-size:6.6px;padding:2px 0;margin-top:3px;text-transform:uppercase;letter-spacing:.3px}
.cover-photo{flex:1;width:100%;margin-top:8px;background:linear-gradient(160deg,#f4f5f7 0%,#d9dde2 45%,#c7ced6 100%)}

/* inside: services */
.panel--services{background:var(--blue);color:#fff;padding-top:26px;border:6px solid var(--paper)}
.services-title{font-size:22px;font-weight:500;margin:10px 0 6px;letter-spacing:.5px}
.service-head{background:var(--paper);color:var(--ink);width:100%;font-size:7.2px;font-weight:600;text-align:center;padding:3px 6px;line-height:1.25}
.service-copy{padding:5px 10px 7px;text-align:center}
.services-phone{margin-top:auto;width:100%;font-size:10px;padding:5px 0}

/* inside: why outsource */
.panel--why{background:var(--paper);padding-top:22px}
.why-head{width:100%;font-size:7.5px;padding:3px 0}
.why-list{display:grid;grid-template-columns:1fr 1fr;gap:2px 8px;list-style:none;font-size:7px;color:var(--ink);padding:7px 20px}
.why-list li::before{content:"";display:inline-block;width:5px;height:5px;border-radius:50%;background:var(--blue);margin-right:4px}
.heartbeat{width:100%;padding:9px 8px;text-transform:uppercase;line-height:1.05}
.heartbeat-small{font-size:10.5px;font-weight:500}
.heartbeat-big{font-size:17px;font-weight:600}
.process-head{width:100%;font-size:7.5px;padding:3px 0;margin-top:10px}
.process-list{list-style:none;width:100%;padding:4px 18px}
.process-list li{font-size:7.2px;color:var(--ink);padding:7px 0;border-bottom:1px solid #dfe2e6}

/* inside: services continued */
.panel--more{background:var(--paper);padding-top:22px}
.more-title{width:100%;font-size:15px;font-weight:500;line-height:1.1;padding:8px 0}
.more-head{font-size:7.5px;font-weight:600;color:var(--ink);padding:5px 0}
.more-copy{width:100%;padding:6px 10px;text-align:center}
</style>
</head>
<body>

<section class="spread spread--outside" aria-label="Brochure outside">
  <article class="panel panel--intro">
    <div class="icon-badge">
      <svg width="26" height="20" viewBox="0 0 26 20" fill="none" stroke="#3aa6dc" stroke-width="1.6" stroke-linejoin="round">
        <path d="M13 4 C9 1.5 5 1.5 2 3 V17 C5 15.5 9 15.5 13 18 C17 15.5 21 15.5 24 17 V3 C21 1.5 17 1.5 13 4 Z"/>
        <path d="M13 4 V18"/>
      </svg>
    </div>
    <h2 class="intro-title">Here to simplify the bookkeeping process</h2>
    <div class="band-dark intro-label">What we do</div>
    <p class="copy intro-copy">Allow business owners to spend more time focusing on their core business by providing comprehensive bookkeeping and business consulting services. We provide the financial data and tools that allow businesses to maximize profitability and focus on growth and other areas of their business. We consider our business to be an extension of your business and look forward to the opportunity to exceed your expectations!</p>
    <div class="brand-name">HL&amp;A</div>
    <div class="band-dark talk">
      <div class="talk-title">LET’S TALK</div>
      <div class="talk-sub">Schedule a no-obligation consultation today</div>
    </div>
  </article>

  <article class="panel panel--back">
    <div class="back-frame">
      <div class="brand-name">HL&amp;A</div>
      <div class="tagline-small">Trustworthy Experienced</div>
      <div class="tagline-big">RELIABLE</div>
      <div class="contact">
        <div class="contact-title">Contact Us:</div>
        <div class="contact-line">marcus@halvickledgers.com</div>
        <div class="contact-line">HALVICK LEDGERS &amp; ADVISORY</div>
        <div class="contact-line">Cedar Valley, PA</div>
        <div class="contact-phone">555.019.4472</div>
      </div>
    </div>
  </article>

  <article class="panel panel--cover">
    <div class="cover-inner">
      <div class="brand-name">HL&amp;A</div>
      <div class="cover-line">Expert bookkeeping services</div>
      <div class="cover-line cover-line--strong">For small businesses</div>
      <div class="band-blue cover-band">Halvick Ledgers &amp; Advisory</div>
      <div class="cover-photo" role="img" aria-label="Photo of a smiling businesswoman at a bright office desk handing over a document"></div>
    </div>
  </article>
</section>

<section class="spread spread--inside" aria-label="Brochure inside">
  <article class="panel panel--services">
    <div class="icon-badge">
      <svg width="18" height="26" viewBox="0 0 18 26" fill="none" stroke="#3aa6dc" stroke-width="1.5" stroke-linecap="round">
        <path d="M9 2 A7 7 0 0 1 13 15 V18 H5 V15 A7 7 0 0 1 9 2 Z"/>
        <path d="M6 21 H12 M7 24 H11"/>
      </svg>
    </div>
    <h2 class="services-title">SERVICES</h2>
    <div class="service-head">Full Charge Bookkeeping</div>
    <p class="copy service-copy">We can manage all aspects of your bookkeeping and business financials and communicate to you as much and as often as you want.</p>
    <div class="service-head">Cash Management (Bill Pay &amp; Invoicing) &amp; Vendor Management</div>
    <p class="copy service-copy">We can handle every step from receiving bills, communicating with vendor and paying bills. We take a lot pride in helping our clients save money and one way is negotiating with vendors and finding appropriate discounts.</p>
    <div class="service-head">Financial Statements</div>
    <p class="copy service-copy">Profit and Loss – Balance Sheet – Statement of Cash Flow – Industry Specific. We accurately prepare monthly, quarterly &amp; annual financial statements in a timely manner. We also take the time to review these statements with you so that you understand the financial health of your business.</p>
    <div class="band-dark services-phone">555.019.4472</div>
  </article>

  <article class="panel panel--why">
    <div class="band-blue why-head">Why Outsource Bookkeeping?</div>
    <ul class="why-list">
      <li>Save Time</li><li>Focused Staff</li>
      <li>Save Money</li><li>Technology</li>
      <li>Expertise</li><li>Experience</li>
    </ul>
    <div class="band-dark heartbeat">
      <div class="heartbeat-small">The financial numbers</div>
      <div class="heartbeat-big">Are the heart</div>
      <div class="heartbeat-small">beat of an organization</div>
    </div>
    <div class="band-blue process-head">The Process</div>
    <ol class="process-list">
      <li>Consultation</li>
      <li>Review of your books</li>
      <li>Recommendations</li>
      <li>Onboarding</li>
      <li>Provide ongoing services</li>
    </ol>
  </article>

  <article class="panel panel--more">
    <h2 class="band-blue more-title">SERVICES<br>(CONTINUED)</h2>
    <div class="more-head">Account Reconciliations</div>
    <p class="copy band-blue more-copy">From bank account to credit card statements to vendor statements, we reconcile all of your accounts that impact your finances.</p>
    <div class="more-head">Professional liaison</div>
    <p class="copy band-blue more-copy">We will work directly with your other business partners – Bankers, CPA, Insurance. Need a loan? We will gather the reports your lender needs.</p>
  </article>
</section>

</body>
</html>
```